Braek down, maintainance and support for satelite and TV

I want a website designed for a Orbitline Engineers firm i want it to look modern. I am finalizing the content with the underwriters at the moment so format we can start on the format and pictures. I want it to be easy to navigate with some eye capturing imiges. I am currently waiting for the underwriters to get the contact over so if we can start on everything else. I ONLY ADDED THE SCREEN SHOT AS I HAD TO ADD SOMETHING TO CONTINUE PLEASE USE YOUR OWN IDEAS

Target Market(s)

Every one

Industry/Entity Type

Tv

Number of Pages Required

5+ page

Font styles to use
Sans Serif

```html
<!DOCTYPE html>
<html lang="en">
<head>
<meta charset="utf-8">
<title>Orbitline Engineers</title>
<link rel="stylesheet" href="https://fonts.googleapis.com/css2?family=Roboto:wght@300;400;500;700&family=Roboto+Condensed:wght@400;700&display=swap">
<style>
:root{
  --red:#e8635a;
  --purple:#4f4052;
  --green:#7cc242;
  --ink:#333333;
  --muted:#6b6b6b;
  --light:#f2f2f2;
  --line:#dcdcdc;
  --footer:#e5e5e5;
  --white:#ffffff;
}
*{box-sizing:border-box;margin:0;padding:0}
html,body{width:1200px;height:2403px;overflow:hidden;background:var(--white)}
body{font-family:'Roboto',Arial,sans-serif;color:var(--ink);position:relative}
.abs{position:absolute}
/* header */
.brand{left:74px;top:40px;display:flex;align-items:center;gap:12px}
.brand-dot{width:26px;height:26px;border-radius:50%;background:var(--red)}
.brand-name{font-size:30px;font-weight:400;color:#3a3a3a;line-height:1.05;letter-spacing:.5px}
.contact-item{top:24px;font-size:13px;line-height:19px;color:#555}
.contact-item svg{display:block;margin-bottom:14px}
.divider{top:30px;width:1px;height:82px;background:var(--line)}
/* nav */
.navbar{left:0;top:138px;width:1200px;height:35px;background:#f4f4f4}
.nav{left:74px;top:138px;display:flex;height:35px}
.nav a{font-size:12.5px;color:#444;text-decoration:none;line-height:35px;padding:0 16px;letter-spacing:.3px}
.nav a.active{background:var(--red);color:var(--white)}
.socials{left:852px;top:142px;display:flex;gap:8px}
.socials span{width:26px;height:26px;border:1.5px solid #bbb;border-radius:50%}
.live{left:984px;top:138px;width:142px;height:35px;background:var(--green);color:var(--white);font-size:13px;display:flex;align-items:center;justify-content:center;gap:8px;font-weight:500}
/* hero */
.hero{left:0;top:173px;width:1200px;height:519px;background:linear-gradient(180deg,#d8dadf 0%,#b7b3ad 45%,#6f7585 75%,#3d5a92 100%)}
.hero-title{left:0;top:494px;width:1200px;text-align:center;font-family:'Roboto',Arial,sans-serif;font-weight:700;font-size:40px;line-height:44px;letter-spacing:-.5px;color:var(--white);text-shadow:0 2px 6px rgba(0,0,0,.35)}
.hero-btn{left:509px;top:603px;width:188px;height:45px;border-radius:23px;background:var(--red);color:var(--white);font-family:'Roboto Condensed',Arial,sans-serif;font-weight:700;font-size:18px;display:flex;align-items:center;justify-content:center}
.arrow-btn{top:410px;width:48px;height:48px;border-radius:50%;background:rgba(255,255,255,.75);display:flex;align-items:center;justify-content:center}
/* services */
.services{left:74px;top:698px;display:flex;gap:7px}
.service{width:170px;height:300px;background:var(--light)}
.service-photo{height:149px}
.service h3{font-size:16.5px;font-weight:400;line-height:19px;color:#333;margin:14px 14px 10px}
.service p{font-size:12.5px;line-height:17px;color:#777;margin:0 14px 12px}
.pill{display:inline-block;font-size:11px;color:#777;background:var(--white);border-radius:10px;padding:3px 12px;margin-left:14px}
/* estimate band */
.band{left:0;top:1045px;width:1200px;height:91px;background:var(--red);color:var(--white);font-family:'Roboto Condensed',Arial,sans-serif;font-weight:700;font-size:29px;display:flex;align-items:center;justify-content:center;gap:12px}
/* welcome */
.welcome-bg{left:0;top:1136px;width:1200px;height:381px;background:#f3f3f3}
.welcome-photo{left:0;top:1136px;width:590px;height:381px;background:linear-gradient(90deg,#e9e9e9 0%,#cfcfcf 55%,#f3f3f3 100%)}
.welcome{left:614px;top:1182px;width:512px}
.welcome h2{font-size:23px;font-weight:400;color:#333;margin-bottom:14px}
.welcome h2 b,.sec-title b{color:var(--red);font-weight:400}
.welcome p{font-size:13.5px;line-height:22px;color:#666}
.trio{display:flex;gap:30px;margin-top:38px}
.trio div{width:150px}
.trio h4{font-size:16px;font-weight:400;margin-bottom:10px}
.trio h4 b{font-weight:500}
.trio p{font-size:13px;line-height:18px}
/* lower */
.sec-title{font-size:23px;font-weight:400;color:#333;padding-bottom:10px;border-bottom:2px solid var(--line)}
.news{left:74px;top:1556px;width:333px}
.news-item{display:flex;gap:20px;margin-top:30px}
.date{width:49px;flex:none;border:2px solid var(--purple);text-align:center;height:64px}
.date b{display:block;font-size:27px;font-weight:400;line-height:40px;color:var(--purple)}
.date span{display:block;background:var(--purple);color:var(--white);font-size:10px;line-height:20px}
.news-item h4{font-size:16px;font-weight:400;line-height:19px;margin-bottom:12px}
.news-item p{font-size:13px;line-height:21px;color:#777}
.more{display:inline-block;margin-top:14px;font-size:11px;color:var(--red);border:1.5px solid var(--red);border-radius:10px;padding:2px 10px}
.quick{left:420px;top:1563px;width:359px;height:504px;background:var(--purple);padding:28px 27px}
.quick h2{font-size:23px;font-weight:400;color:var(--white);margin-bottom:18px}
.quick h2 b{font-weight:500}
.field{height:41px;border:1px solid #8d7f90;margin-bottom:18px;font-size:13px;color:#c9c0cb;padding:11px 12px}
.field.msg{height:89px}
.submit{display:inline-flex;align-items:center;gap:8px;border:2px solid var(--white);color:var(--white);font-weight:700;font-size:15px;padding:8px 18px;margin-top:2px}
.testi{left:793px;top:1556px;width:333px}
.quote{background:#f2f2f2;padding:16px 18px;margin-top:28px;font-size:13px;line-height:22px;color:#666;position:relative}
.author{font-size:15px;color:var(--red);margin:22px 0 0 50px}
/* footer */
.footer{left:0;top:2115px;width:1200px;height:288px;background:var(--footer);border-top:8px solid var(--red)}
.f-col{top:2156px;font-size:12.5px;line-height:26px;color:#666}
.f-col h5{font-size:15px;font-weight:500;color:#333;margin-bottom:8px}
.f-brand{left:74px;top:2170px;display:flex;align-items:center;gap:12px}
.f-brand .brand-name{color:#8a8a8a;font-size:27px}
.f-socials{left:74px;top:2278px;display:flex;gap:8px}
.f-socials span{width:32px;height:32px;border:2px solid #999;border-radius:50%}
.f-copy{left:74px;top:2326px;font-size:12px;line-height:17px;color:#666}
.f-input{height:36px;background:var(--white);border-radius:4px;margin-top:10px;font-size:12.5px;color:#999;display:flex;align-items:center;gap:8px;padding-left:14px;width:243px}
.subscribe{margin-top:10px;width:243px;height:36px;background:var(--purple);color:var(--white);border-radius:4px;font-size:14px;font-weight:700;display:flex;align-items:center;justify-content:center}
</style>
</head>
<body>

<header>
  <div class="abs brand"><span class="brand-dot"></span><span class="brand-name">Orbitline<br>Engineers</span></div>

  <div class="abs contact-item" style="left:564px">
    <svg width="22" height="28" viewBox="0 0 22 28"><path d="M11 2a8 8 0 0 0-8 8c0 6 8 16 8 16s8-10 8-16a8 8 0 0 0-8-8z" fill="none" stroke="#e8635a" stroke-width="1.8"/><circle cx="11" cy="10" r="3" fill="none" stroke="#e8635a" stroke-width="1.8"/></svg>
    42 Harbour Lane,<br>Westbridge, 204417
  </div>
  <div class="abs divider" style="left:735px"></div>
  <div class="abs contact-item" style="left:772px">
    <svg width="28" height="28" viewBox="0 0 28 28"><path d="M7 3l5 5-3 3c1.5 3 4 5.5 7 7l3-3 5 5-3.5 3.5C13 23 5 15 3.5 6.5z" fill="none" stroke="#e8635a" stroke-width="1.8" stroke-linejoin="round"/></svg>
    Need Help? Call Us<br>+44 (0)7000 555 20 40
  </div>
  <div class="abs divider" style="left:935px"></div>
  <div class="abs contact-item" style="left:970px">
    <svg width="30" height="28" viewBox="0 0 30 28"><rect x="2" y="6" width="26" height="18" fill="none" stroke="#e8635a" stroke-width="1.8"/><path d="M2 6l13 10 13-10" fill="none" stroke="#e8635a" stroke-width="1.8"/></svg>
    Email Us :<br>hello@orbitline.example
  </div>
</header>

<div class="abs navbar"></div>
<nav class="abs nav">
  <a class="active">HOME</a><a>ABOUT US</a><a>SERVICES</a><a>NEWS</a><a>TESTIMONIALS</a><a>CONTACT US</a>
</nav>
<div class="abs socials"><span></span><span></span><span></span><span></span></div>
<div class="abs live">
  <svg width="16" height="16" viewBox="0 0 16 16"><circle cx="8" cy="5" r="3.5" fill="#fff"/><path d="M1 16c0-4 3-6 7-6s7 2 7 6z" fill="#fff"/></svg>
  LIVE SUPPORT
</div>

<section>
  <div class="abs hero" role="img" aria-label="Friends watching sport on a wall-mounted television in a living room"></div>
  <div class="abs arrow-btn" style="left:74px"><svg width="14" height="20" viewBox="0 0 14 20"><path d="M11 2L3 10l8 8" fill="none" stroke="#555" stroke-width="2.5"/></svg></div>
  <div class="abs arrow-btn" style="left:1077px"><svg width="14" height="20" viewBox="0 0 14 20"><path d="M3 2l8 8-8 8" fill="none" stroke="#555" stroke-width="2.5"/></svg></div>
  <h1 class="abs hero-title">DUIS AUTEM VEL EUM IRIURE DOLOR IN<br>HENDRERIT IN VULPUTATE VELIT</h1>
  <div class="abs hero-btn">GET STARTED</div>
</section>

<section class="abs services">
  <article class="service"><div class="service-photo" role="img" aria-label="Viewer switching channels with a remote" style="background:linear-gradient(135deg,#3b5270,#8d9fb5)"></div><h3>Switch to<br>Digital</h3><p>Imperdiet doming id tationem lectorum.</p><span class="pill">MORE</span></article>
  <article class="service"><div class="service-photo" role="img" aria-label="Engineer fitting a satellite dish to a wall" style="background:linear-gradient(135deg,#a4573f,#9db0c6)"></div><h3>Service and<br>Repairs</h3><p>Imperdiet doming id tationem lectorum.</p><span class="pill">MORE</span></article>
  <article class="service"><div class="service-photo" role="img" aria-label="Stack of banknotes" style="background:linear-gradient(135deg,#7e7a58,#c3bc94)"></div><h3>No Hidden<br>Charges</h3><p>Imperdiet doming id tationem lectorum.</p><span class="pill">MORE</span></article>
  <article class="service"><div class="service-photo" role="img" aria-label="Television mounted on a living room wall" style="background:linear-gradient(135deg,#e7e4df,#8a8078)"></div><h3>TV Wall<br>Mounting</h3><p>Imperdiet doming id tationem lectorum.</p><span class="pill">MORE</span></article>
  <article class="service"><div class="service-photo" role="img" aria-label="Technician in overalls holding a television" style="background:linear-gradient(135deg,#dfe3e8,#3d5a90)"></div><h3>Same Day<br>Service</h3><p>Imperdiet doming id tationem lectorum.</p><span class="pill">MORE</span></article>
  <article class="service"><div class="service-photo" role="img" aria-label="Happy couple giving a thumbs up" style="background:linear-gradient(135deg,#e2ddd6,#6d8fb8)"></div><h3>Work<br>Guaranteed</h3><p>Imperdiet doming id tationem lectorum.</p><span class="pill">MORE</span></article>
</section>

<div class="abs band">REQUEST A FREE ESTIMATES FOR ORBITLINE ENGINEERS
  <svg width="30" height="30" viewBox="0 0 30 30"><circle cx="15" cy="15" r="12.5" fill="none" stroke="#fff" stroke-width="2.5"/><path d="M12 9l6 6-6 6" fill="none" stroke="#fff" stroke-width="2.5"/></svg>
</div>

<div class="abs welcome-bg"></div>
<div class="abs welcome-photo" role="img" aria-label="Support agents wearing headsets in a call centre, in black and white"></div>
<section class="abs welcome">
  <h2>WELCOME TO <b>ORBITLINE ENGINEERS</b></h2>
  <p>Lorem ipsum dolor sit amet, consectetuer adipiscing elit, sed diam nonummy nibh euismod tincidunt ut laoreet dolore magna aliquam erat volutpat. Ut wisi enim ad minim veniam, quis nostrud exerci tation ullamcorper suscipit lobortis nisl ut aliquip ex ea commodo consequat. Duis autem vel eum iriure dolor in hendrerit in vulputate velit esse molestie consequat.</p>
  <div class="trio">
    <div><h4>Our <b>Mission</b></h4><p>Lorem Ipsum has been dummy text ever since the 1500s.</p></div>
    <div><h4>Our <b>Vision</b></h4><p>Lorem Ipsum has been dummy text ever since the 1500s.</p></div>
    <div><h4>Our <b>Value</b></h4><p>Lorem Ipsum has been dummy text ever since the 1500s.</p></div>
  </div>
</section>

<section class="abs news">
  <h2 class="sec-title">LATEST <b>NEWS</b></h2>
  <div class="news-item">
    <div class="date"><b>19</b><span>JAN,16</span></div>
    <div><h4>Duis autem vel eum iriure dolor in hendrerit in vulputate</h4><p>Lorem ipsum dolor sit amet, conse ctetuer adipiscing elit, sed dianummy nibh euismod tincidunt ut laoreet dolore magna aliquam erat.</p><span class="more">MORE</span></div>
  </div>
  <div class="news-item" style="margin-top:38px">
    <div class="date"><b>24</b><span>JAN,16</span></div>
    <div><h4>Duis autem vel eum iriure dolor in hendrerit in vulputate</h4><p>Lorem ipsum dolor sit amet, conse ctetuer adipiscing elit, sed dianummy nibh euismod tincidunt ut laoreet dolore magna aliquam erat.</p><span class="more">MORE</span></div>
  </div>
</section>

<section class="abs quick">
  <h2>QUICK <b>CONTACT</b></h2>
  <div class="field">First Name</div>
  <div class="field">Last Name</div>
  <div class="field">Email Address</div>
  <div class="field">Phone</div>
  <div class="field msg">Message</div>
  <span class="submit">SUBMIT <svg width="22" height="18" viewBox="0 0 22 18"><path d="M1 8L21 1l-5 16-5-6z" fill="#fff"/></svg></span>
</section>

<section class="abs testi">
  <h2 class="sec-title">CLIENT <b>TESTIMONIALS</b></h2>
  <div class="quote">“Lorem ipsum dolor sit amet, consectetuer adipiscing elit, sed diam nonummy nibh euismod tincidunt ut laoreet dolore magna aliquam erat volutpat. Ut wisi enim ad minim veniam, quis nostrud exerci tation ullamcorper ut aliquip ex ea commodo consequat.”</div>
  <div class="author">- Mark Bennett</div>
  <div class="quote" style="margin-top:28px">“Lorem ipsum dolor sit amet, consectetuer adipiscing elit, sed diam nonummy nibh euismod tincidunt ut laoreet dolore magna aliquam erat volutpat. Ut wisi enim ad minim veniam, quis nostrud exerci tation ullamcorper ut aliquip ex ea commodo consequat.”</div>
  <div class="author">- Clara Hughes</div>
</section>

<footer>
  <div class="abs footer"></div>
  <div class="abs f-brand"><span class="brand-dot" style="background:#9a9a9a"></span><span class="brand-name">Orbitline<br>Engineers</span></div>
  <div class="abs f-socials"><span></span><span></span><span></span></div>
  <div class="abs f-copy">© 2016 Orbitline Engineers<br>All Rights Reserved.</div>

  <div class="abs f-col" style="left:343px">
    <h5>Important Links</h5>
    Switch to Digital<br>Service and Repairs<br>No Hidden Charges<br>TV Wall Mounting<br>Same Day Service<br>Work Guaranteed
  </div>
  <div class="abs f-col" style="left:614px;line-height:17px">
    <h5 style="margin-bottom:14px">Contact Us</h5>
    <b style="font-weight:500;color:#444">Orbitline Engineers</b><br>42 Harbour Lane,<br>Westbridge, 204417<br><br><br>T : +44 (0)7000 555 20 40<br>F : +44 (0)7000 555<br><br><br>E : hello@orbitline.example<br>W: www.orbitline.example
  </div>
  <div class="abs f-col" style="left:883px;line-height:17px">
    <h5 style="margin-bottom:14px">Subscribe Newsletter - Today!</h5>
    Enter your name and email to subscribe<br>our newsletters &amp; receive latest offers!!!
    <div class="f-input"><svg width="12" height="12" viewBox="0 0 12 12"><circle cx="6" cy="4" r="2.5" fill="#aaa"/><path d="M1 12c0-3 2-4.5 5-4.5s5 1.5 5 4.5z" fill="#aaa"/></svg>Enter Your Name</div>
    <div class="f-input"><svg width="13" height="10" viewBox="0 0 13 10"><rect x="0.5" y="0.5" width="12" height="9" fill="none" stroke="#aaa"/><path d="M.5 .5l6 5 6-5" fill="none" stroke="#aaa"/></svg>Enter Your Email</div>
    <div class="subscribe">SUBSCRIBE</div>
  </div>
</footer>

</body>
</html>
```